1876 Basins & Spouts Business Card

I'm wanting to get a business card designed. Our business is 1876 Basins & Spouts
Details for the card:

1876 Basins & Spouts
Name: Harold Vesk
Email: harold@1876basinsandspouts.com.au
Website: www.1876basinsandspouts.com.au
Mobile: 0438 260 947
Phone: 02 7481 3926

Font of Basins & Spouts is called Snell Roundhand. Not sue what font logo text is.

I'm thinking two sided but it doesn't have to be.

```html
<!DOCTYPE html>
<html lang="en">
<head>
<meta charset="utf-8">
<title>1876 Basins &amp; Spouts Business Card</title>
<link rel="stylesheet" href="https://fonts.googleapis.com/css2?family=Open+Sans:wght@400;600&family=Arimo:wght@700&display=swap">
<style>
  :root {
    --stage: #d9d9d9;
    --paper: #ffffff;
    --ink: #1a1a1a;
    --ink-soft: #444444;
    --rule: #b5b5b5;
    --tint: #ececec;
    --night: #1c1a1b;
    --night-pattern: #2a2728;
    --frost: #f2f2f2;
  }
  * { box-sizing: border-box; margin: 0; padding: 0; }
  html, body { width: 1200px; height: 782px; overflow: hidden; }
  body {
    background: var(--stage);
    font-family: "Open Sans", Arial, sans-serif;
    color: var(--ink);
    position: relative;
  }
  .card {
    position: absolute;
    top: 241px;
    width: 540px;
    height: 300px;
    box-shadow: 0 6px 18px rgba(0,0,0,0.25);
    overflow: hidden;
  }
  .card--front { left: 40px; background: var(--paper); }
  .card--back { left: 620px; background: var(--night); }

  .brand {
    position: absolute;
    left: 28px;
    top: 40px;
    width: 170px;
    display: flex;
    flex-direction: column;
    align-items: center;
    text-align: center;
    gap: 10px;
  }
  .brand__dot {
    width: 54px; height: 54px;
    border: 2px solid var(--ink);
    border-radius: 50%;
  }
  .brand__name {
    font-size: 19px;
    font-weight: 400;
    color: var(--ink);
    line-height: 1.2;
  }
  .brand__tagline {
    font-size: 8px;
    color: var(--ink-soft);
    line-height: 1.4;
  }
  .divider {
    position: absolute;
    left: 215px;
    top: 30px;
    width: 1px;
    height: 220px;
    background: var(--rule);
  }
  .year-mark {
    position: absolute;
    right: 0;
    top: 40px;
    width: 120px;
    height: 260px;
    background: linear-gradient(160deg, var(--paper) 0%, var(--tint) 60%, var(--paper) 100%);
  }
  .person {
    position: absolute;
    left: 238px;
    top: 56px;
    right: 20px;
  }
  .person__name {
    font-family: "Arimo", Arial, sans-serif;
    font-weight: 700;
    font-size: 20px;
    letter-spacing: 0.5px;
    text-transform: uppercase;
    margin-bottom: 40px;
  }
  .contact { list-style: none; }
  .contact__item {
    display: flex;
    align-items: center;
    gap: 8px;
    font-size: 15px;
    line-height: 22px;
    color: var(--ink-soft);
    white-space: nowrap;
  }
  .contact__icon { width: 12px; height: 12px; flex: none; }

  .pattern {
    position: absolute;
    inset: 0;
    background: radial-gradient(circle at 50% 50%, var(--night-pattern) 0%, var(--night) 70%);
  }
  .back-mark {
    position: absolute;
    left: 50%;
    top: 50%;
    transform: translate(-50%, -50%);
    display: flex;
    align-items: center;
    gap: 10px;
    color: var(--frost);
  }
  .back-mark__dot {
    width: 26px; height: 26px;
    border: 1.5px solid var(--frost);
    border-radius: 50%;
  }
  .back-mark__name { font-size: 17px; font-weight: 400; }
</style>
</head>
<body>

<section class="card card--front" aria-label="Business card front">
  <div class="brand">
    <div class="brand__dot"></div>
    <p class="brand__name">1876 Basins &amp; Spouts</p>
    <p class="brand__tagline">Classic fixtures for modern homes and lasting style</p>
  </div>
  <div class="divider"></div>
  <div class="year-mark" role="img" aria-label="Large faint brand year decoration"></div>
  <div class="person">
    <h1 class="person__name">Harold Vesk</h1>
    <ul class="contact">
      <li class="contact__item">
        <svg class="contact__icon" viewBox="0 0 12 12"><path d="M2 1h3l1 3-2 1a7 7 0 0 0 3 3l1-2 3 1v3c-6 0-9-3-9-9z" fill="#1a1a1a"/></svg>
        0438 260 947
      </li>
      <li class="contact__item">
        <svg class="contact__icon" viewBox="0 0 12 12"><rect x="1.5" y="1.5" width="9" height="9" rx="1.5" fill="none" stroke="#1a1a1a" stroke-width="1.5"/></svg>
        02 7481 3926
      </li>
      <li class="contact__item">
        <svg class="contact__icon" viewBox="0 0 12 12"><rect x="0.5" y="2" width="11" height="8" fill="#1a1a1a"/><path d="M1 2.5l5 4 5-4" fill="none" stroke="#fff" stroke-width="1"/></svg>
        harold@1876basinsandspouts.com.au
      </li>
      <li class="contact__item">
        <svg class="contact__icon" viewBox="0 0 12 12"><circle cx="6" cy="6" r="5.5" fill="#1a1a1a"/><path d="M0.5 6h11M6 0.5v11" stroke="#fff" stroke-width="0.8"/></svg>
        www.1876basinsandspouts.com.au
      </li>
    </ul>
  </div>
</section>

<section class="card card--back" aria-label="Business card back">
  <div class="pattern" role="img" aria-label="Repeating pattern of faint brand emblems"></div>
  <div class="back-mark">
    <div class="back-mark__dot"></div>
    <p class="back-mark__name">1876 Basins &amp; Spouts</p>
  </div>
</section>

</body>
</html>
```